Oriel Photography Business Card

I need a business card designed for a photography business based in Perth, Western Australia called Oriel Photography.

We specialise in wedding, event photography and portrait photography.

The business card must borrow the style of the attached logo.

The hex codes for the colours in the logo are:
#ED1D85 - Pink
#89C23E - Green
#37282F - Black

The name on the card will be:
Name: Tobrian
Phone: 0417395268
Website: www.orielphotography.example.com.au
Facebook: orielphotography

I am open and happy to accept creative concepts.

I’d like some space at the back for writing notes and appointment details.

```html
<!DOCTYPE html>
<html lang="en">
<head>
<meta charset="utf-8">
<title>Oriel Photography Business Card</title>
<link href="https://fonts.googleapis.com/css2?family=Open+Sans:wght@400;600;700&family=Raleway:wght@400;500&display=swap" rel="stylesheet">
<style>
  :root {
    --pink: #ED1D85;
    --green: #89C23E;
    --ink: #37282F;
    --paper: #ffffff;
    --backdrop: #ecebe8;
    --rule: #9a9596;
  }
  * { box-sizing: border-box; margin: 0; padding: 0; }
  html, body { width: 1200px; height: 720px; overflow: hidden; }
  body {
    background: var(--backdrop);
    font-family: "Open Sans", Arial, sans-serif;
    color: var(--ink);
    position: relative;
  }
  .card {
    position: absolute;
    top: 195px;
    width: 540px;
    height: 315px;
    background: var(--paper);
    box-shadow: 0 2px 10px rgba(0,0,0,0.12);
    overflow: hidden;
  }
  .card--front { left: 40px; }
  .card--back { left: 620px; }

  .brand {
    position: absolute;
    left: 0; right: 0;
    text-align: center;
  }
  .brand__mark {
    display: block;
    width: 58px; height: 58px;
    margin: 0 auto 12px;
    border-radius: 50%;
    background: var(--pink);
  }
  .brand__name {
    font-family: "Raleway", Arial, sans-serif;
    font-weight: 400;
    font-size: 15px;
    letter-spacing: 0.62em;
    text-transform: uppercase;
    color: var(--ink);
    padding-left: 0.62em;
  }
  .card--front .brand { top: 22px; }
  .card--back .brand { top: 26px; }

  .holder {
    position: absolute;
    top: 124px; left: 0; right: 0;
    text-align: center;
    font-weight: 700;
    font-size: 19px;
    letter-spacing: 0.04em;
    text-transform: uppercase;
    color: var(--pink);
  }
  .contact-band {
    position: absolute;
    left: 0; right: 0; bottom: 0;
    top: 160px;
    background: var(--pink);
    border-top: 4px solid var(--paper);
    box-shadow: 0 -3px 0 var(--green);
    padding-top: 34px;
    text-align: center;
  }
  .contact-band ul { list-style: none; }
  .contact-band li {
    display: flex;
    justify-content: center;
    align-items: center;
    gap: 8px;
    color: var(--paper);
    font-size: 14px;
    line-height: 28px;
  }
  .contact-band svg { width: 14px; height: 14px; flex: none; }
  .bullet {
    width: 12px; height: 12px;
    border-radius: 50%;
    background: var(--paper);
    flex: none;
  }

  .notes {
    position: absolute;
    left: 22px; right: 28px;
    top: 140px;
  }
  .notes__line {
    height: 30px;
    border-bottom: 1px dotted var(--rule);
    position: relative;
  }
  .notes__line--labelled { display: flex; align-items: flex-end; }
  .notes__label {
    font-weight: 600;
    font-size: 17px;
    color: #1d1d1d;
    padding-right: 6px;
    line-height: 1;
    position: relative;
    top: 2px;
    background: var(--paper);
  }
  .web {
    position: absolute;
    left: 0; right: 0; bottom: 20px;
    text-align: center;
    font-size: 15px;
    letter-spacing: 0.06em;
    color: var(--ink);
  }
</style>
</head>
<body>
  <section class="card card--front" aria-label="Card front">
    <div class="brand">
      <span class="brand__mark" aria-hidden="true"></span>
      <p class="brand__name">Oriel Photography</p>
    </div>
    <p class="holder">Tobrian</p>
    <div class="contact-band">
      <ul>
        <li>
          <svg viewBox="0 0 16 16" aria-hidden="true"><circle cx="8" cy="8" r="8" fill="#fff"/><path d="M5.2 4.2l1.4-.2.8 2-.9.8c.5 1.1 1.3 1.9 2.4 2.4l.8-.9 2 .8-.2 1.4c-3.6.2-6.5-2.7-6.3-6.3z" fill="var(--pink)"/></svg>
          <span>0417395268</span>
        </li>
        <li><span class="bullet" aria-hidden="true"></span><span>orielphotography</span></li>
        <li><span class="bullet" aria-hidden="true"></span><span>www.orielphotography.example.com.au</span></li>
      </ul>
    </div>
  </section>

  <section class="card card--back" aria-label="Card back">
    <div class="brand">
      <span class="brand__mark" aria-hidden="true"></span>
      <p class="brand__name">Oriel Photography</p>
    </div>
    <div class="notes">
      <div class="notes__line notes__line--labelled"><span class="notes__label">notes:</span></div>
      <div class="notes__line"></div>
      <div class="notes__line"></div>
    </div>
    <p class="web">www.orielphotography.example.com.au</p>
  </section>
</body>
</html>
```